Otter Bites Guild - A Monthly Subscription Dog Treats Club - Shopify Website Design

A monthly subscription company. Need a Shopify Website Design and uploaded to fully work with Crisp Renewals.

Please look at these sites for examples as well as the images I enclosed.

https://www.mealbrightly.com/
https://www.globalmunchbox.com/

Number of Pages Required

1 page

```html
<!DOCTYPE html>
<html lang="en">
<head>
<meta charset="utf-8">
<title>Otter Bites Guild – Dog Treats Club</title>
<link href="https://fonts.googleapis.com/css2?family=Montserrat:wght@400;500;600&family=Oswald:wght@400;500&family=Lobster&display=swap" rel="stylesheet">
<style>
:root{
  --pink:#e63e7a;
  --ink:#333333;
  --muted:#555555;
  --grey-btn:#6f6f6f;
  --line:#cfcfcf;
  --soft:#f4f4f4;
  --footer:#3b3b3b;
  --white:#ffffff;
}
*{box-sizing:border-box;margin:0;padding:0}
html,body{width:1200px;height:2853px;overflow:hidden;background:var(--white)}
body{position:relative;font-family:"Montserrat",sans-serif;color:var(--ink)}
.abs{position:absolute}

/* header */
.brand{left:172px;top:22px;display:flex;align-items:center;gap:10px;font-family:"Oswald",sans-serif;font-weight:500;font-size:30px;color:var(--pink);letter-spacing:.5px}
.brand-dot{width:14px;height:14px;border-radius:50%;background:var(--pink)}
.search{left:489px;top:23px;width:232px;height:41px;border:2px solid #9a9a9a;font-size:13px;padding:11px 8px;color:var(--ink)}
.account{left:733px;top:34px;font-size:14px;font-weight:500}
.account span{margin:0 6px}
.cart{left:1004px;top:30px}
.header-rule{left:172px;top:88px;width:855px;height:1px;background:#888}
.nav{left:0;top:113px;width:1200px;display:flex;justify-content:center;gap:0}
.nav a{font-size:16px;color:var(--ink);text-decoration:none;letter-spacing:.3px}
.nav-list{position:absolute;left:270px;top:113px;width:760px;height:22px}
.nav-list a{position:absolute;font-size:16px;color:var(--ink);text-decoration:none;letter-spacing:.3px}

/* hero */
.hero{left:0;top:156px;width:1200px;height:607px;background:linear-gradient(100deg,#3a2a22 0%,#4a362b 40%,#5b4333 70%,#4a3427 100%)}
.hero-goods{left:540px;top:240px;width:660px;height:470px;border-radius:40px;background:radial-gradient(ellipse at 55% 55%,rgba(214,60,60,.55),rgba(40,150,140,.35) 45%,rgba(230,170,40,.2) 70%,rgba(0,0,0,0) 80%)}
.hero-title{left:172px;top:328px;font-family:"Lobster",cursive;font-size:64px;color:var(--white);letter-spacing:1px}
.hero-sub{left:172px;top:412px;font-family:"Lobster",cursive;font-size:36px;color:var(--white)}
.hero-btn{left:174px;top:503px;width:121px;height:51px;border:3px solid var(--white);color:var(--white);font-weight:600;font-size:16px;display:flex;align-items:center;justify-content:center;letter-spacing:.5px}

/* promo tiles */
.tile{top:827px;width:272px;height:186px;color:var(--white);text-align:center;overflow:hidden}
.tile-dark{left:172px;background:linear-gradient(135deg,#2f2f2f,#5a5a5a)}
.tile-pink{left:464px;background:linear-gradient(135deg,#e8407c,#d62f6c)}
.tile-wood{left:756px;background:linear-gradient(135deg,#6d5238,#8c6a48 55%,#4f3b2a)}
.tile-top{margin-top:27px;font-size:20px}
.tile-rule{width:178px;height:1px;background:rgba(255,255,255,.7);margin:8px auto}
.tile-main{font-size:34px;font-weight:600;line-height:44px}
.tile-bottom{font-size:23px;margin-top:12px}

/* products */
.card{width:201px;height:258px;border:1px solid var(--line);background:var(--white)}
.photo{position:absolute;left:14px;right:14px;top:50px;bottom:50px;border-radius:14px}
.pname{font-family:"Oswald",sans-serif;font-size:20px;color:var(--ink);letter-spacing:.2px}
.price{font-family:"Oswald",sans-serif;font-size:16px;color:var(--ink)}
.price.hot{color:var(--pink)}
.btn{width:104px;height:48px;color:var(--white);font-family:"Oswald",sans-serif;font-size:16px;display:flex;align-items:center;justify-content:center;background:var(--grey-btn)}
.btn.hot{background:var(--pink)}

.featured{left:0;top:1588px;width:1200px;height:547px;background:var(--soft)}
.section-title{font-family:"Oswald",sans-serif;font-size:24px;color:var(--ink)}

/* newsletter */
.news-title{left:172px;top:2214px}
.news-copy{left:172px;top:2262px;width:510px;font-size:14.5px;line-height:24px;color:var(--muted)}
.field{border:1px solid #bdbdbd;background:var(--white);font-size:14px;color:var(--muted);padding-left:10px;display:flex;align-items:center}
.go{background:var(--pink);color:var(--white);font-size:14px;display:flex;align-items:center;justify-content:center}
.news-photo{left:718px;top:2199px;width:444px;height:274px;border-radius:30px 30px 0 0;background:linear-gradient(160deg,#4a3a3e,#5e4b4f 50%,#e9ddd0 75%,#c2485f)}

/* footer */
.footer{left:0;top:2473px;width:1200px;height:380px;background:var(--footer);color:var(--white)}
.foot-head{font-family:"Oswald",sans-serif;font-size:22px;color:var(--white)}
.foot-text{font-size:12.5px;line-height:22.5px;color:#eeeeee}
.social{width:30px;height:30px;border-radius:50%;background:var(--white)}
.foot-rule{left:172px;top:2762px;width:855px;height:1px;background:#8a8a8a}
.copy{left:172px;top:2802px;font-size:14px;color:#eeeeee}
.pay{top:2806px;width:27px;height:17px;border-radius:2px;background:#e9e9e9}
</style>
</head>
<body>

<header>
  <div class="abs brand"><span class="brand-dot"></span>Otter Bites Guild</div>
  <div class="abs search">Search here...</div>
  <div class="abs account">Sign in<span>|</span>Create account<span>|</span>Checkout</div>
  <svg class="abs cart" width="24" height="26" viewBox="0 0 24 26" aria-label="Cart">
    <path d="M3 8h18l-1.5 16h-15z" fill="none" stroke="#e63e7a" stroke-width="2" stroke-linejoin="round"/>
    <path d="M8 10V6a4 4 0 0 1 8 0v4" fill="none" stroke="#e63e7a" stroke-width="2"/>
  </svg>
  <div class="abs header-rule"></div>
  <nav class="nav-list">
    <a style="left:0">HOME</a>
    <a style="left:93px">SHOP</a>
    <a style="left:188px">BLOG</a>
    <a style="left:281px">ABOUT US</a>
    <a style="left:411px">CONTACT</a>
    <a style="left:535px">OUR FEATURES</a>
  </nav>
</header>

<section class="abs hero" role="img" aria-label="Dark wooden backdrop with pet bowls, grooming brushes, toys and treats"></section>
<div class="abs hero-goods" role="img" aria-label="Assorted pet bowls, brushes, notepad and toys"></div>
<h1 class="abs hero-title">Dog Treats Club</h1>
<p class="abs hero-sub">Monthly Subscription</p>
<div class="abs hero-btn">SHOP NOW</div>

<section>
  <div class="abs tile tile-dark" role="img" aria-label="Grooming tools on dark background">
    <div class="tile-top">NEW</div><div class="tile-rule"></div>
    <div class="tile-main">ARRIVALS</div><div class="tile-rule"></div>
    <div class="tile-bottom">DAILY</div>
  </div>
  <div class="abs tile tile-pink" role="img" aria-label="Scissors and brush under pink tint">
    <div class="tile-top">3 DAYS</div><div class="tile-rule"></div>
    <div class="tile-main">SAVE 30%</div><div class="tile-rule"></div>
    <div class="tile-bottom">ONLY</div>
  </div>
  <div class="abs tile tile-wood" role="img" aria-label="Dog accessories on wooden table">
    <div class="tile-top">DOG</div><div class="tile-rule"></div>
    <div class="tile-main">ACCESSORIES</div><div class="tile-rule"></div>
    <div class="tile-bottom">AVAILABLE</div>
  </div>
</section>

<section class="products">
  <div class="abs card" style="left:172px;top:1089px"><div class="photo" role="img" aria-label="Small dog holding a grooming brush" style="background:linear-gradient(#f2e6da,#d9b890)"></div></div>
  <div class="abs card" style="left:390px;top:1089px"><div class="photo" role="img" aria-label="Retractable leash and tennis ball toy" style="background:linear-gradient(90deg,#8a8a8a,#7ca0c0,#d8e48a)"></div></div>
  <div class="abs card" style="left:607px;top:1089px"><div class="photo" role="img" aria-label="Small dog inside a wire crate" style="background:linear-gradient(#e8e8e8,#9a9a9a)"></div></div>
  <div class="abs card" style="left:825px;top:1089px"><div class="photo" role="img" aria-label="Stainless steel dog bowl" style="background:linear-gradient(#e5e5e5,#ffffff)"></div></div>

  <div class="abs pname" style="left:172px;top:1358px">NAM LIBERO TEMPORE</div>
  <div class="abs pname" style="left:390px;top:1358px">NAM LIBERO TEMPORE</div>
  <div class="abs pname" style="left:607px;top:1358px">NAM LIBERO TEMPORE</div>
  <div class="abs pname" style="left:825px;top:1358px">NAM LIBERO TEMPORE</div>
  <div class="abs price hot" style="left:172px;top:1394px">$29.00 USD</div>
  <div class="abs price" style="left:390px;top:1394px">$29.00 USD</div>
  <div class="abs price" style="left:607px;top:1394px">$29.00 USD</div>
  <div class="abs price" style="left:825px;top:1394px">$29.00 USD</div>
  <div class="abs btn hot" style="left:172px;top:1434px">ADD TO CART</div>
  <div class="abs btn" style="left:390px;top:1434px">ADD TO CART</div>
  <div class="abs btn" style="left:607px;top:1434px">ADD TO CART</div>
  <div class="abs btn" style="left:825px;top:1434px">ADD TO CART</div>
</section>

<section class="abs featured"></section>
<h2 class="abs section-title" style="left:0;top:1647px;width:1200px;text-align:center">OUR FEATURED COLLECTIONS</h2>
<div class="abs card" style="left:172px;top:1730px"><div class="photo" role="img" aria-label="Basket of colourful dog toys" style="background:linear-gradient(90deg,#f5a623,#e8406a,#3cb8d8)"></div></div>
<div class="abs card" style="left:390px;top:1730px"><div class="photo" role="img" aria-label="Tan leather dog harness" style="background:linear-gradient(#e9d4bc,#c9a27c)"></div></div>
<div class="abs card" style="left:607px;top:1730px"><div class="photo" role="img" aria-label="Collar, red bowl, bone and rope ball" style="background:linear-gradient(90deg,#8a5a3c,#d42a2a,#7cc84a)"></div></div>
<div class="abs card" style="left:825px;top:1730px"><div class="photo" role="img" aria-label="Puppy lying with rope toys" style="background:linear-gradient(#c8854a,#9a6a48)"></div></div>
<div class="abs pname" style="left:172px;top:1998px">NAM LIBERO TEMPORE</div>
<div class="abs pname" style="left:390px;top:1998px">NAM LIBERO TEMPORE</div>
<div class="abs pname" style="left:607px;top:1998px">NAM LIBERO TEMPORE</div>
<div class="abs pname" style="left:825px;top:1998px">NAM LIBERO TEMPORE</div>
<div class="abs price hot" style="left:172px;top:2034px">$29.00 USD</div>
<div class="abs price" style="left:390px;top:2034px">$29.00 USD</div>
<div class="abs price" style="left:607px;top:2034px">$29.00 USD</div>
<div class="abs price" style="left:825px;top:2034px">$29.00 USD</div>

<section>
  <h2 class="abs section-title news-title">SUBSCRIBE TO OUR NEWSLETTER</h2>
  <p class="abs news-copy">Enter your email address below to join our mailing list and have our latest news and member-only deals delivered straight to your inbox.</p>
  <div class="abs field" style="left:172px;top:2350px;width:414px;height:49px">Email</div>
  <div class="abs go" style="left:585px;top:2350px;width:81px;height:49px">GO</div>
  <div class="abs news-photo" role="img" aria-label="Fluffy puppy sitting in an open suitcase with toys"></div>
</section>

<footer class="abs footer"></footer>
<h3 class="abs foot-head" style="left:172px;top:2556px">WELCOME</h3>
<p class="abs foot-text" style="left:173px;top:2606px;width:234px;text-align:justify">Nam libero tempore, cum soluta nobis est eligendi optio cumque nihil im pedit quo minus id quod maxime placeat facere possimus, omnis.</p>
<h3 class="abs foot-head" style="left:472px;top:2556px">NEWSLETTER</h3>
<p class="abs foot-text" style="left:473px;top:2606px;width:320px">Sign up to stay in the loop. Receive updates, access to exclusive deals, and more.</p>
<div class="abs field" style="left:473px;top:2667px;width:234px;height:48px;border:none">Email</div>
<div class="abs go" style="left:706px;top:2667px;width:75px;height:48px">GO</div>
<h3 class="abs foot-head" style="left:850px;top:2556px">SOCIAL LINKS</h3>
<div class="abs social" style="left:851px;top:2614px"></div>
<div class="abs social" style="left:900px;top:2614px"></div>
<div class="abs social" style="left:948px;top:2614px"></div>
<div class="abs social" style="left:997px;top:2614px"></div>
<div class="abs foot-rule"></div>
<p class="abs copy">Copyrights @ 2020 Otter Bites Guild. All Rights Reserved.</p>
<div class="abs pay" style="left:840px"></div>
<div class="abs pay" style="left:872px"></div>
<div class="abs pay" style="left:904px"></div>
<div class="abs pay" style="left:936px"></div>
<div class="abs pay" style="left:968px"></div>
<div class="abs pay" style="left:1000px"></div>

</body>
</html>
```